Global (re)insurance broker needs a business card design

We need a classic business card for our company that is headquartered in SG, with offices in Malaysia and Dubai. We specialise in insurance and reinsurance broking and consultancy for our global clients.

```html
<!DOCTYPE html>
<html lang="en">
<head>
<meta charset="utf-8">
<title>Norvane Business Card</title>
<link rel="stylesheet" href="https://fonts.googleapis.com/css2?family=Open+Sans:wght@400;600;700&display=swap">
<style>
  :root {
    --page: #2a2a2e;
    --card: #1f1e23;
    --edge: #c8e4c2;
    --mint: #c8e4c2;
    --blue: #2c4da3;
    --ink: #f2f2f2;
    --emboss: #2b2a30;
  }
  * { margin: 0; padding: 0; box-sizing: border-box; }
  html, body {
    width: 1200px; height: 780px; overflow: hidden;
    background: var(--page);
    font-family: "Open Sans", sans-serif;
  }
  .canvas {
    position: relative; width: 1200px; height: 780px;
    display: flex; align-items: center; justify-content: center; gap: 50px;
  }
  .card {
    position: relative; width: 540px; height: 310px;
    background: var(--card);
    border-radius: 24px;
    border: 2px solid var(--edge);
    overflow: hidden;
  }
  .emboss-name {
    position: absolute; color: var(--emboss);
    font-weight: 700; letter-spacing: 2px; white-space: nowrap;
  }
  .card-front .emboss-name {
    font-size: 82px; left: 50%; top: 50%; transform: translate(-50%, -50%);
  }
  .card-back .emboss-name {
    font-size: 52px; right: 26px; bottom: 26px;
  }
  .brand-name {
    position: absolute; left: 34px; top: 112px;
    font-size: 46px; font-weight: 700; color: var(--mint); letter-spacing: 1px;
  }
  .accent-bar {
    position: absolute; right: 0; top: 0; width: 22px; height: 70px;
    background: var(--mint);
  }
  .person {
    position: absolute; right: 44px; top: 18px; text-align: left;
  }
  .person-name { font-size: 34px; font-weight: 700; line-height: 1.05; }
  .person-name .first { color: var(--blue); }
  .person-name .last { color: var(--mint); }
  .person-title { font-size: 14px; color: var(--ink); margin-top: 2px; }
  .address {
    position: absolute; left: 34px; top: 190px;
    font-size: 13px; color: var(--ink); line-height: 1.35;
  }
  .contacts {
    position: absolute; left: 34px; top: 232px; list-style: none;
    font-size: 13px; color: var(--ink); line-height: 1.45;
  }
  .contacts li { display: flex; align-items: center; gap: 8px; }
  .contacts svg { width: 12px; height: 12px; flex: none; }
</style>
</head>
<body>
<main class="canvas">
  <section class="card card-front" aria-label="Card front">
    <span class="emboss-name">NORVANE</span>
  </section>

  <section class="card card-back" aria-label="Card back">
    <div class="accent-bar"></div>
    <div class="person">
      <p class="person-name"><span class="first">Mira</span> <span class="last">Lowe</span></p>
      <p class="person-title">Chief Operating Officer</p>
    </div>
    <span class="brand-name">NORVANE</span>
    <p class="address">28 Harbour Street, Meridian<br>Tower #08-04, Singapore 048562</p>
    <ul class="contacts">
      <li>
        <svg viewBox="0 0 12 12"><rect x="3" y="0.5" width="6" height="11" rx="1.2" fill="none" stroke="var(--ink)" stroke-width="1"/></svg>
        +65 9123 4567
      </li>
      <li>
        <svg viewBox="0 0 12 12"><circle cx="6" cy="6" r="5.5" fill="var(--blue)"/><path d="M0.5 6h11M6 0.5c-2.5 3-2.5 8 0 11M6 0.5c2.5 3 2.5 8 0 11" stroke="var(--ink)" stroke-width="0.6" fill="none"/></svg>
        www.norvane.com
      </li>
      <li>
        <svg viewBox="0 0 12 12"><rect x="0.5" y="2.5" width="11" height="8" fill="none" stroke="var(--ink)" stroke-width="1"/><path d="M0.5 2.5l5.5 4.5 5.5-4.5" fill="none" stroke="var(--ink)" stroke-width="1"/></svg>
        mira@norvane.com
      </li>
    </ul>
    <span class="emboss-name">NORVANE</span>
  </section>
</main>
</body>
</html>
```